Site re-branding and modernization

Two Managed Service Providers (Information Technology) have merged and need an update to their website. The site needs to be re-branded from "Ridgeline Computing" with a blue theme to "Harbor Systems" with an orange theme.

Harbor Systems provides small and medium business with an outsourced IT department, offering enterprise level IT to business that otherwise wouldn't have it. Our marketing has been centered around a row of apples with one orange and a caption that says, "We do IT our own way and we're happy about it!" Hence the orange color scheme needed as well as a site that stands out from the typical MSP site.

We would like to maintain our current site in order to retain SEO, update the technology used (current site is flash based), mobile (Zelphone, Zelpad, Orbitel Phone) compatible and Color Theme update (likely orange and white).

My current site:
http://www.harborsystems-example.net

My chief local competition (who we want to look better than):
http://www.quillbyte-example.com/

Other MSP sites (people we want to stand out from):
http://www.lanternops-example.com/
http://www.fernacle-example.com/
Updates

Please send your email to mpatterly@harborsys-example.com if you are interested in this project so I can send you a filecrate link to the existing site files for you to work with.

https://www.filecrate-example.com/sh/4k2pq8wzrbn51tx/QQL9MvaHsT2ZwpeuNoXKA74b

We would like to have a Call to action form on the main page and an informational Video. In addition we would like the following Categories and coorisponding Icons on the Main Page. We will also need a page for each Sub-Category. The Tag line on the Landing Page / Banner should read "Enterprise Solutions for Everyone" Managed IT >Law Firms .>Associations / Nonprofits > Financial Services > Healthcare >Education Cloud Services >Server > Desktop >Managed Wireless > Voice > Restaurant Point of Sale >Pellmark Suite 365 Migrations Data Center > Managed Servers > Managed Desktops >Disaster Recovery Hosting Professional Services >Virtualization >Backup & DR Planning >Corvane Links >Mobile or Virtual Office Solutions

Target Market(s)

Small and medium business that want to have the best possible IT support.

Industry/Entity Type

Marketing

Colors
f37022

Requirements
Must have
• Convert Site from Flash to Latest web design technology i.e. DHTML. Site must be mobile friendly. Convert all Ridgeline Computing Logo Marks to Harbor Systems Logo. Change Color Theme to match uploaded files.

```html
<!DOCTYPE html>
<html lang="en">
<head>
<meta charset="utf-8">
<title>Harbor Systems — Internet Marketing</title>
<link href="https://fonts.googleapis.com/css2?family=Lato:ital,wght@0,400;0,700;0,900;1,400&family=Oswald:wght@400;500&display=swap" rel="stylesheet">
<style>
:root{
  --orange:#f37022;
  --orange-light:#f9a65a;
  --black:#000;
  --white:#fff;
  --footer:#3b3f3e;
  --footer-text:#e4e4e4;
  --player:#333;
  --ink:#111;
  --panel:rgba(0,0,0,.6);
}
*{margin:0;padding:0;box-sizing:border-box}
html,body{width:748px;height:1200px;overflow:hidden;background:var(--white)}
body{font-family:'Lato',sans-serif;color:var(--ink);position:relative}
.utility-bar{position:absolute;top:0;left:0;width:748px;height:22px;background:var(--black);display:flex;justify-content:flex-end;align-items:center;padding-right:14px;font-size:9.5px;font-weight:700;color:var(--white)}
.utility-bar span{margin:0 5px}
.utility-bar .muted{font-weight:400;color:#ddd}
.site-header{position:absolute;top:22px;left:0;width:748px;height:75px}
.brand{position:absolute;left:20px;top:14px;display:flex;align-items:flex-start;gap:6px}
.brand-mark{width:18px;height:18px;background:var(--orange);margin-top:2px}
.brand-name{font-size:12px;font-weight:700;color:var(--ink);line-height:1.1;letter-spacing:.3px}
.brand-tagline{font-size:6.5px;color:var(--ink);position:absolute;left:0;top:36px;width:160px}
.social{position:absolute;right:20px;top:14px;display:flex;gap:12px}
.social span{width:20px;height:20px;border-radius:50%;background:var(--orange);display:block}
.call{position:absolute;right:26px;top:52px;font-family:'Oswald',sans-serif;font-size:14px;color:var(--ink);letter-spacing:.2px}
.call b{font-weight:500;margin-left:14px}
.main-nav{position:absolute;top:97px;left:0;width:748px;height:54px;background:var(--orange);font-size:13px;color:var(--black)}
.main-nav a{position:absolute;top:0;height:54px;line-height:54px;color:inherit;text-decoration:none}
.main-nav .active{background:var(--black);color:var(--white);left:98px;width:162px;padding-left:14px}
.hero{position:absolute;left:17px;top:152px;width:708px;height:299px;box-shadow:0 2px 6px rgba(0,0,0,.45);overflow:hidden}
.hero-image{position:absolute;inset:0;background:radial-gradient(circle at 22% 55%,#1f6fc4 0%,#0d3a7a 30%,rgba(255,255,255,0) 48%),linear-gradient(90deg,#eef4fb 0%,#cfe3f4 40%,#5a9bd0 70%,#2a6fb0 100%)}
.hero-tagline{position:absolute;left:22px;bottom:22px;width:380px;font-size:27px;line-height:30px;font-weight:900;color:var(--white);text-shadow:0 1px 4px rgba(0,0,0,.6)}
.cta-form{position:absolute;right:18px;top:26px;width:214px;padding:14px 14px 16px;background:var(--panel);color:var(--white)}
.cta-form h2{font-size:13px;font-weight:700;margin-bottom:10px}
.cta-form .field{display:block;width:100%;height:24px;margin-bottom:7px;background:var(--white);border:0;font:9px 'Lato',sans-serif;color:#777;padding:0 8px;line-height:24px}
.cta-form .submit{display:block;width:100%;height:28px;margin-top:4px;background:var(--orange);color:var(--white);font:700 11px 'Lato',sans-serif;text-align:center;line-height:28px;text-transform:uppercase;letter-spacing:.4px}
.services{position:absolute;top:487px;left:0;width:748px;height:225px;background:var(--orange);color:var(--white)}
.services h1{position:absolute;left:22px;top:20px;font-size:29px;font-weight:400;color:var(--orange-light);letter-spacing:.5px}
.services h1 strong{font-weight:900;letter-spacing:1px}
.services .copy{position:absolute;left:22px;top:75px;width:460px;font-size:8.6px;line-height:11px}
.services .copy p{margin-bottom:12px}
.service-list{position:absolute;right:27px;top:56px;list-style:none;font-size:15px;font-weight:700;line-height:16px;text-transform:uppercase}
.service-list li{display:flex;justify-content:flex-end;align-items:center;gap:6px}
.service-list svg{flex:none}
.service-list .current{color:var(--orange-light);font-weight:400}
.learn{position:absolute;top:712px;left:0;width:748px;height:225px}
.learn-label{position:absolute;right:492px;top:100px;font-size:18px;font-weight:700;color:var(--ink)}
.learn-label em{font-weight:400}
.video{position:absolute;left:273px;top:0;width:475px;height:225px;background:var(--black)}
.play{position:absolute;left:214px;top:73px;width:65px;height:65px;border-radius:6px;background:var(--player)}
.play svg{position:absolute;left:22px;top:21px}
.site-footer{position:absolute;top:937px;left:0;width:748px;height:263px;background:var(--footer);color:var(--footer-text)}
.footer-col{position:absolute;top:47px;width:130px}
.footer-col h2{font-size:12px;font-weight:700;color:var(--white);margin-bottom:14px}
.footer-col ul{list-style:none;font-size:8.8px;line-height:10.6px}
.footer-col .strong{color:var(--white);font-weight:700}
.footer-col .indent{padding-left:20px}
.legal{position:absolute;top:199px;left:0;width:748px;text-align:center;font-size:8.8px;color:var(--white)}
.legal span{margin:0 9px}
</style>
</head>
<body>
<div class="utility-bar">
  <span>Home</span>|<span>Submit Trouble Ticket</span>|<span class="muted">Pay Bill Online</span>|<span>Blog</span>|<span>Client Login</span>
</div>
<header class="site-header">
  <div class="brand">
    <span class="brand-mark"></span>
    <div class="brand-name">HARBOR<br>SYSTEMS.NET</div>
    <div class="brand-tagline">We do IT our own way and we're happy about it!</div>
  </div>
  <div class="social" aria-label="Social links">
    <span aria-label="Social profile"></span>
    <span aria-label="Social profile"></span>
    <span aria-label="Blog"></span>
  </div>
  <div class="call">CALL TODAY <b>(866) 555-0142</b></div>
</header>
<nav class="main-nav">
  <a style="left:20px">IT SERVICES</a>
  <a class="active">INTERNET MARKETING</a>
  <a style="left:282px">ABOUT</a>
  <a style="left:349px">CONTACT US</a>
</nav>
<section class="hero">
  <div class="hero-image" role="img" aria-label="Globe surrounded by streaming panels of digital media imagery"></div>
  <div class="hero-tagline">Enterprise Solutions for Everyone</div>
  <form class="cta-form">
    <h2>Request a Free Consultation</h2>
    <span class="field">Name</span>
    <span class="field">Email</span>
    <span class="field">Phone</span>
    <span class="submit">Get Started</span>
  </form>
</section>
<section class="services">
  <h1>Our <strong>TOP-LEVEL</strong> <em>SERVICES</em></h1>
  <div class="copy">
    <p>The Internet is the most widely used source for finding any type of information in the world. More and more businesses are steering clear of print and turning to Internet marketing and advertising. This is because it generates business. When you want to look up a product or service, do you go to the phone book, or the Internet? People who are going to the Internet to find their answers are typically clicking one of the first six links that are displayed by the search engines. You can be one of those six with our Internet marketing service.</p>
    <p>Harbor Systems specializes in delivering Santa Fe and Tucson Arizona two of the most beneficial forms of Internet Advertising; worldwide Search Engine Optimization (SEO) services and managing multi-level Pay Per Click (PPC) campaigns. Our team of Internet Specialists will optimize your visibility and guarantee traffic to your website.</p>
  </div>
  <ul class="service-list">
    <li><svg width="12" height="12" viewBox="0 0 12 12" aria-hidden="true"><circle cx="6" cy="6" r="4.5" fill="none" stroke="#fff" stroke-width="1.5"/><circle cx="6" cy="6" r="1.5" fill="#fff"/></svg>Managed IT</li>
    <li><svg width="12" height="12" viewBox="0 0 12 12" aria-hidden="true"><rect x="1" y="4" width="10" height="7" fill="none" stroke="#fff" stroke-width="1.5"/><path d="M4 4V2h4v2" fill="none" stroke="#fff" stroke-width="1.5"/></svg>Small &amp; Mid-Size Businesses</li>
    <li class="current"><svg width="12" height="12" viewBox="0 0 12 12" aria-hidden="true"><path d="M6 1v10M2 11h8M1 4h10M3 4l-2 4h4zM9 4l-2 4h4z" fill="none" stroke="#f9a65a" stroke-width="1.2"/></svg>Law Firms</li>
    <li><svg width="12" height="12" viewBox="0 0 12 12" aria-hidden="true"><circle cx="4" cy="4" r="2" fill="#fff"/><circle cx="8.5" cy="4" r="2" fill="#fff"/><path d="M0.5 11a3.5 3.5 0 0 1 7 0zM5.5 11a3 3 0 0 1 6 0z" fill="#fff"/></svg>Associations / Non-Profits</li>
    <li><svg width="12" height="12" viewBox="0 0 12 12" aria-hidden="true"><path d="M1 11h10M2 10V7M5 10V4M8 10V1.5" fill="none" stroke="#fff" stroke-width="1.8"/></svg>Financial Services</li>
    <li><svg width="12" height="12" viewBox="0 0 12 12" aria-hidden="true"><path d="M4.5 1h3v3.5H11v3H7.5V11h-3V7.5H1v-3h3.5z" fill="#fff"/></svg>Healthcare</li>
    <li><svg width="12" height="12" viewBox="0 0 12 12" aria-hidden="true"><path d="M6 2L0.5 5 6 8l5.5-3zM3 6.5V9.5c1.5 1.2 4.5 1.2 6 0V6.5" fill="#fff"/></svg>Education</li>
  </ul>
</section>
<section class="learn">
  <div class="learn-label">Learn <em>MORE</em></div>
  <div class="video">
    <div class="play">
      <svg width="22" height="24" viewBox="0 0 22 24"><path d="M2 1 L20 12 L2 23 Z" fill="#000"/></svg>
    </div>
  </div>
</section>
<footer class="site-footer">
  <div class="footer-col" style="left:37px">
    <h2>Top Level Services</h2>
    <ul><li>Managed IT</li><li class="strong">Small &amp; Mid-Size Businesses</li><li>Law Firms</li><li>Associations / Non-Profits</li><li>Financial Services</li><li>Healthcare</li><li>Education</li></ul>
  </div>
  <div class="footer-col" style="left:172px">
    <h2>Cloud Services</h2>
    <ul><li>Backup &amp; Disaster Recovery</li><li>Public &amp; Private Cloud Server Solutions</li><li>Voice</li><li>Pellmark Suite 365 Migrations</li><li>Restaurant Point of Sale</li></ul>
  </div>
  <div class="footer-col" style="left:306px">
    <h2>Data Center</h2>
    <ul><li>Managed Servers</li><li>DR Hosting</li><li>Virtual Office Solutions</li></ul>
  </div>
  <div class="footer-col" style="left:440px">
    <h2>Professional Services</h2>
    <ul><li>Virtualization</li><li>Corvane Links</li><li>Virtual Office Design &amp;</li><li class="indent">Deployment</li><li>Restaurant POS Design &amp;</li><li class="indent">Deployment</li></ul>
  </div>
  <div class="footer-col" style="left:575px">
    <h2>About Us</h2>
    <ul><li>Who we are</li><li>Testimonials</li><li>Partners</li><li>Locations</li><li>Site</li></ul>
  </div>
  <div class="legal"><span>franchise opportunites</span>|<span>terms</span>|<span>privacy policy</span></div>
</footer>
</body>
</html>
```